Professional Engineering Web Design

Project Brief: Website Redesign for Mechanical Design Consultancy
Project Overview
I want to update and improve my current website to create a more professional, modern, and high-credibility online presence for my mechanical design consultancy.

Current site: https://valtorix.design/

The new website must communicate expertise, precision, and trust—matching the standard of top engineering and product design agencies.

Reference Websites (Style + Structure Inspiration)
These represent the quality, cleanliness, and professionalism I want to achieve:

https://plinthwaredesign.com/
https://www.sorvane.com/
https://bramlow-uk.com/
Brand Look
Professional, modern, engineering-focused aesthetic
Clean layouts and strong typography
High-quality imagery conveying precision, innovation, and mechanical expertise
Colour scheme and styling must follow my existing logo (attached in project)
Platform Requirements
The website must be built on WordPress
Should use a clean, flexible theme or modern page builder (Elementor, Gutenberg, Bricks, or similar)
Avoid overly complex custom coding so I can easily edit content later
Final deliverable must allow me to manage and update content without developer assistance
Functionality
Fast-loading, lightweight, and smooth user experience
Clean animations and transitions similar to the reference sites
Fully mobile responsive
Clear navigation and strong visual hierarchy
Contact forms optimised for lead generation
Optional: subtle scroll effects, case study sliders, icon animations, etc.
SEO Aspirations
Developer should recommend and implement a modern SEO strategy
Proper on-page SEO setup (titles, meta, schema, alt tags, heading structure)
Optimised site architecture for ranking and crawling
Aim: Generate leads through improved visibility and keyword targeting
Optional but useful: Google Analytics, Google Search Console setup
User Journeys
(Recommended structure)

The site should be crafted around clear, intuitive journeys for each type of visitor:

Potential new clients
Quickly understand what services I offer
View examples of past work / case studies
See credibility indicators (process, expertise, industries served)
Easily contact me or request a project discussion
Returning clients
Access updated portfolio items
Find contact details or book follow-up work easily
General visitors discovering through SEO
Be guided to core service areas
Understand my value proposition quickly
Be invited to learn more or make contact
The developer should design the structure to support these journeys smoothly.

Maintenance Expectations
Website will be maintained by me, so it should be easy to update using relatively basic WordPress skills
Use modular templates and simple backend structure
Avoid unnecessary plugins
Provide brief handover documentation if required
Hosting Preferences
Site is currently hosted via a family member
Open to discussing moving to a paid, reliable hosting provider if preferable for performance and maintainability
Developer may advise on the best hosting setup for WordPress
Content
Most content can be taken from the existing website
Developer is welcome to suggest improvements to structure, layout, and imagery
Must remain easy for me to edit or add new content later (e.g., new projects)
Deliverables
Fully built WordPress website
Clean, professional, modern design inspired by the reference sites
Mobile-responsive across all devices
SEO-ready structure and optimisations
Transfer of website and admin rights
Any design assets, templates, or documentation used

```html
<!DOCTYPE html>
<html lang="en">
<head>
<meta charset="utf-8">
<title>Valtorix Mechanical Design</title>
<link rel="stylesheet" href="https://fonts.googleapis.com/css2?family=Montserrat:wght@400;500;600;700&display=swap">
<style>
:root{--navy:#1b1784;--blue:#2a3de0;--ink:#1d1d22;--text:#3c3c46;--grey:#ebebee;--white:#fff;}
*{margin:0;padding:0;box-sizing:border-box}
html,body{width:1200px;height:4769px;overflow:hidden}
body{position:relative;font-family:'Montserrat',sans-serif;color:var(--ink);background:var(--white)}
.abs{position:absolute}
.header{top:0;left:0;width:1200px;height:102px;background:#fff;z-index:3}
.brand{left:120px;top:26px;display:flex;align-items:center;gap:14px}
.brand-dot{width:48px;height:48px;border-radius:50%;background:var(--blue)}
.brand-name{font-size:30px;font-weight:600;color:var(--navy);letter-spacing:1px}
.contact-bar{left:612px;top:12px;display:flex;gap:40px;font-size:14px;align-items:center}
.contact-bar span{display:flex;align-items:center;gap:10px}
.ic{width:32px;height:32px;border-radius:50%;background:var(--blue);display:inline-flex;align-items:center;justify-content:center}
.nav{left:450px;top:62px;display:flex;gap:36px;font-size:13px;font-weight:500}
.nav .active{font-weight:700;border-bottom:2px solid var(--ink)}
.search{left:926px;top:51px;width:152px;height:38px;border:1.5px solid #333;border-radius:4px;font-size:12px;padding:10px 10px;color:#555}
.hero{top:102px;left:0;width:1200px;height:666px}
.hero-photo{position:absolute;inset:0;background:linear-gradient(110deg,#2b3038 0%,#55606c 45%,#1e2a3a 75%,#0f1a2a 100%)}
.hero-text{left:124px;top:208px;color:#fff}
.hero-text .kicker{font-size:17px;font-weight:600;letter-spacing:.3px}
.hero-text h1{font-size:72px;font-weight:600;line-height:80px;margin-top:14px}
.hero-text p{font-size:32px;font-weight:400;margin-top:4px}
.btn{display:inline-block;background:var(--navy);color:#fff;font-size:13px;font-weight:700;padding:14px 27px}
.section-title{font-size:40px;font-weight:600;text-align:center}
.section-title em{font-style:normal;color:var(--navy)}
.bar{width:56px;height:4px;background:var(--navy);margin:14px auto 0}
.welcome{top:850px;left:0;width:1200px;text-align:center}
.welcome h3{font-size:29px;font-weight:500}
.welcome h2{font-size:40px;font-weight:600;color:var(--navy);margin-top:8px}
.welcome p{font-size:20px;line-height:32px;color:var(--text);margin:30px auto 0;width:820px}
.expertise{top:1093px;left:0;width:1200px}
.card{top:1218px;width:298px;height:278px;background:#fff;border-radius:10px;box-shadow:0 2px 12px rgba(0,0,0,.16);text-align:center;padding:26px 30px}
.card.on{background:var(--navy);color:#fff}
.card .circ{width:80px;height:80px;border-radius:50%;border:2px dashed currentColor;margin:0 auto;display:flex;align-items:center;justify-content:center}
.card .circ i{width:60px;height:60px;border-radius:50%;background:var(--navy);display:block}
.card.on .circ i{background:#2c2a96}
.card h4{font-size:21px;font-weight:700;line-height:29px;margin-top:26px}
.card p{font-size:13px;line-height:24px;margin-top:10px}
.work{top:1586px;left:0;width:1200px}
.work .sub{font-size:19px;text-align:center;margin-top:28px;color:var(--text)}
.acc{left:131px;width:940px;background:#fff;box-shadow:0 2px 10px rgba(0,0,0,.18);border-radius:3px}
.acc-head{height:78px;display:flex;align-items:center;justify-content:space-between;padding:0 32px;font-size:24px;font-weight:600}
.tri{width:0;height:0;border-left:8px solid transparent;border-right:8px solid transparent;border-top:10px solid var(--ink)}
.acc-open{top:1748px;height:310px}
.acc-photo{left:8px;top:8px;width:382px;height:294px;background:radial-gradient(circle at 45% 50%,#d5d7dc 0,#8c9096 40%,#eceef0 75%);border:1px solid #ddd}
.acc-body{left:426px;top:40px;width:480px}
.acc-body h4{font-size:24px;font-weight:600}
.acc-body p{font-size:13.5px;line-height:24px;color:var(--text);margin-top:16px}
.acc-body .btn{margin-top:20px;padding:12px 32px}
.about-band{top:2600px;left:0;width:1200px;height:1400px}
.about{left:121px;top:2770px;width:440px;color:#fff}
.about h2{font-size:40px;font-weight:600}
.about .bar{margin:24px 0 0;background:#fff}
.about h5{font-size:18px;font-weight:700;line-height:24px;margin-top:34px}
.about p{font-size:13.5px;line-height:24px;margin-top:2px}
.about .btn{background:#1d1d22;margin-top:30px;font-size:13px;padding:12px 18px}
.portrait{left:638px;top:2728px;width:408px;height:408px;border-radius:50%;background:radial-gradient(circle,#6a5a52 0,#3a3f5a 70%);box-shadow:16px 6px 0 #2b2b2b}
.rule{left:120px;top:3191px;width:960px;height:2px;background:rgba(255,255,255,.6)}
.feedback{left:0;top:3296px;width:1200px;color:#fff}
.feedback h2{font-size:40px;line-height:50px}
.feedback .bar{background:#fff;margin-top:24px}
.quote{top:3450px;width:456px;height:323px;background:#fff;border-radius:4px;padding:26px 26px}
.stars{color:#f0a500;font-size:20px;letter-spacing:2px}
.quote p{font-size:13.5px;line-height:26.5px;color:var(--text);margin-top:12px}
.quote b{display:block;color:var(--navy);font-size:16px;margin-top:14px}
.quote small{font-size:13px;color:var(--text)}
.arrow{top:3588px;width:36px;height:36px;border:2px solid #fff;border-radius:50%}
.curious{top:4060px;left:0;width:1200px;text-align:center}
.curious .btn{margin-top:46px;padding:13px 45px}
.footer{left:0;top:4330px;width:1200px;height:439px}
.f-brand{left:162px;top:4470px;font-size:34px;font-weight:600;color:var(--navy);display:flex;gap:12px;align-items:center}
.f-col{top:4424px;font-size:14px}
.f-col h6{font-size:16px;font-weight:600;margin-bottom:18px}
.f-col li{list-style:none;margin-bottom:14px;color:var(--text)}
.f-col li::before{content:"➔ ";font-size:12px;color:var(--ink)}
.f-contact li::before{content:none}
.f-contact li{display:flex;gap:14px;line-height:24px}
.f-contact .ic{flex:none;width:30px;height:30px}
.f-rule{left:120px;top:4654px;width:960px;height:2px;background:#555}
.copy{left:0;top:4683px;width:1200px;text-align:center;font-size:10.5px;line-height:19px;color:var(--text)}
.copy p:last-child{margin-top:8px;font-size:12px}
</style>
</head>
<body>
<header class="header abs">
  <div class="brand abs"><span class="brand-dot"></span><span class="brand-name">valtorix</span></div>
  <div class="contact-bar abs">
    <span><i class="ic"><svg width="16" height="16" viewBox="0 0 24 24"><path fill="#fff" d="M6.6 10.8a15 15 0 0 0 6.6 6.6l2.2-2.2c.3-.3.7-.4 1-.2 1.1.4 2.3.6 3.6.6.6 0 1 .4 1 1V20c0 .6-.4 1-1 1A17 17 0 0 1 3 4c0-.6.4-1 1-1h3.5c.6 0 1 .4 1 1 0 1.3.2 2.5.6 3.6.1.3 0 .7-.2 1z"/></svg></i>07700 900412</span>
    <span><i class="ic"><svg width="16" height="16" viewBox="0 0 24 24"><path fill="#fff" d="M3 5h18v14H3zm2 2v.5l7 4.5 7-4.5V7z"/></svg></i>rowan@valtorixstudio.co.uk</span>
  </div>
  <nav class="nav abs"><span class="active">HOME</span><span>PORTFOLIO</span><span>OUR SERVICES</span><span>CONTACT US</span></nav>
  <div class="search abs">Search</div>
</header>

<section class="hero abs">
  <div class="hero-photo" role="img" aria-label="Machined gear assembly in front of engineering CAD screens"></div>
  <svg class="abs" style="left:0;top:0" width="1200" height="666" viewBox="0 0 1200 666"><path fill="#fff" d="M0 520 C250 640 560 700 800 650 C1000 610 1130 540 1200 510 L1200 666 L0 666Z"/></svg>
  <div class="hero-text abs" style="top:106px">
    <div class="kicker">WELCOME TO VALTORIX MECHANICAL DESIGN</div>
    <h1>Mechanical<br>CAD Design</h1>
    <p>Cutting Edge Engineering</p>
    <a class="btn" style="margin-top:26px">VIEW OUR SERVICES</a>
  </div>
</section>

<section class="welcome abs">
  <h3>Welcome to</h3>
  <h2>Valtorix Mechanical Design</h2>
  <div class="bar"></div>
  <p>We are a UK based design consultancy offering a comprehensive mechanical and product design service from initial concepts through to full volume production.</p>
</section>

<section class="expertise abs">
  <h2 class="section-title">Our <em>Expertise</em></h2>
  <div class="bar"></div>
</section>
<div class="card on abs" style="left:120px"><div class="circ"><i></i></div><h4>Bespoke<br>Product Design</h4><p>Innovative design from concept through the full development life cycle</p></div>
<div class="card abs" style="left:450px"><div class="circ" style="color:var(--navy)"><i></i></div><h4>3D Modelling and Drawings</h4><p>We create 3D CAD, 2D engineering drawings and photorealistic renders</p></div>
<div class="card abs" style="left:780px"><div class="circ" style="color:var(--navy)"><i></i></div><h4>Design for<br>Manufacture</h4><p>Creating designs optimised for prototype and production manufacture</p></div>

<section class="work abs">
  <h2 class="section-title">Our <em>Work</em></h2>
  <div class="bar"></div>
  <p class="sub">A small selection of our previous projects</p>
</section>
<div class="acc acc-open abs">
  <div class="acc-photo abs" role="img" aria-label="Polished three-piece alloy wheel"></div>
  <div class="acc-body abs">
    <h4>3-Piece Alloy Wheels</h4>
    <p>We have been working on a long term project to bring custom 3-piece Japanese style wheels to market since 2020.<br>We have completed all aspects of design, development, project management and business work on this project from concepts through to production.</p>
    <a class="btn">READ MORE</a>
  </div>
  <div class="tri abs" style="right:24px;top:48px;transform:rotate(180deg)"></div>
</div>
<div class="acc abs" style="top:2076px"><div class="acc-head">Go-Kart Simulator Design<i class="tri"></i></div></div>
<div class="acc abs" style="top:2167px"><div class="acc-head">3-Piece Alloy Wheels<i class="tri"></i></div></div>
<div class="acc abs" style="top:2260px"><div class="acc-head">Dual Clutch Transmission Design<i class="tri"></i></div></div>
<div class="acc abs" style="top:2352px"><div class="acc-head">Electrical Switchgear<i class="tri"></i></div></div>
<div class="acc abs" style="top:2445px"><div class="acc-head">ORVELLE Luxury Pen<i class="tri"></i></div></div>

<svg class="about-band abs" width="1200" height="1400" viewBox="0 0 1200 1400"><path fill="var(--navy)" d="M0 150 C200 40 420 20 620 40 C850 60 1050 80 1200 120 L1200 1170 C1100 1340 900 1390 700 1370 C450 1340 200 1250 0 1240Z"/></svg>
<section class="about abs">
  <h2>About Rowan Ellery</h2>
  <div class="bar"></div>
  <h5>Rowan Ellery is the Chief Engineer at<br>Valtorix Mechanical Design.</h5>
  <p>He has 11 years experience working as a mechanical design engineer in multiple industries including high performance automotive, consumer products, medical, industrial plus many more. He has worked in multiple roles across a wide range of</p>
  <a class="btn">TELL US ABOUT YOUR IDEAS</a>
</section>
<div class="portrait abs" role="img" aria-label="Portrait photo of the chief engineer"></div>
<div class="rule abs"></div>
<section class="feedback abs">
  <h2 class="section-title" style="font-weight:500">Feedback from some of our<br>recent customers</h2>
  <div class="bar"></div>
</section>
<div class="arrow abs" style="left:43px"><svg width="32" height="32" viewBox="0 0 32 32"><path d="M21 16H11m4-5-5 5 5 5" stroke="#fff" stroke-width="2" fill="none"/></svg></div>
<div class="arrow abs" style="left:1121px"><svg width="32" height="32" viewBox="0 0 32 32"><path d="M11 16h10m-4-5 5 5-5 5" stroke="#fff" stroke-width="2" fill="none"/></svg></div>
<div class="quote abs" style="left:137px"><div class="stars">★★★★★</div><p>Rowan was amazing. His communication was excellent, responded very quickly, started working on the project the same day I purchased, and problem solved every little detail with my design. He clearly knows what he is talking about and has put in all his efforts to create a perfect design. I highly recommend his service and will use him again on my next project.</p><b>Nerys</b><small>Manager</small></div>
<div class="quote abs" style="left:615px"><div class="stars">★★★★★</div><p>"Rowan is able to bridge the gap between what management want and what manufacturing can deliver. In the field of Casting his intuition for the process and knowledge of casting technical nuances means he is able to push both the design and guide manufacturers to produce excellent results.</p><b style="margin-top:30px">Gareth Lowen</b><small>Design Engineer</small></div>

<section class="curious abs">
  <h2 class="section-title" style="font-weight:500">Curious <em>what else we do?</em></h2>
  <div class="bar"></div>
  <a class="btn">SEE HERE</a>
</section>

<svg class="footer abs" width="1200" height="439" viewBox="0 0 1200 439"><path fill="var(--grey)" d="M0 120 C150 40 350 10 600 30 C850 50 1050 80 1200 60 L1200 439 L0 439Z"/></svg>
<div class="f-brand abs"><span class="brand-dot" style="width:40px;height:40px"></span>valtorix</div>
<div class="f-col abs" style="left:424px"><h6>MAIN LINKS</h6><ul><li>Home Page</li><li>Portfolio</li><li>Our Services</li><li>Contact Us</li></ul></div>
<div class="f-col abs" style="left:624px"><h6>OTHER LINKS</h6><ul><li>Privacy Policy</li><li>Support Links</li><li>Terms of Use</li></ul></div>
<div class="f-col f-contact abs" style="left:835px;width:260px"><h6>CONTACT US</h6><ul>
  <li><i class="ic"><svg width="14" height="14" viewBox="0 0 24 24"><path fill="#fff" d="M12 2a7 7 0 0 0-7 7c0 5 7 13 7 13s7-8 7-13a7 7 0 0 0-7-7zm0 9.5A2.5 2.5 0 1 1 12 6a2.5 2.5 0 0 1 0 5.5z"/></svg></i>Mill Yard, Brenhill,<br>Wales, CF00 1AB.</li>
  <li><i class="ic"><svg width="14" height="14" viewBox="0 0 24 24"><path fill="#fff" d="M6.6 10.8a15 15 0 0 0 6.6 6.6l2.2-2.2c.3-.3.7-.4 1-.2 1.1.4 2.3.6 3.6.6.6 0 1 .4 1 1V20c0 .6-.4 1-1 1A17 17 0 0 1 3 4c0-.6.4-1 1-1h3.5c.6 0 1 .4 1 1 0 1.3.2 2.5.6 3.6.1.3 0 .7-.2 1z"/></svg></i>+44 (0) 7700 900518</li>
  <li><i class="ic"><svg width="14" height="14" viewBox="0 0 24 24"><path fill="#fff" d="M3 5h18v14H3zm2 2v.5l7 4.5 7-4.5V7z"/></svg></i>info@valtorix.design</li>
</ul></div>
<div class="f-rule abs"></div>
<div class="copy abs">
  <p>Halden Wheels Ltd trading as Valtorix Product Design. Registered in Wales. Company No. 14820391.<br>Registered Office: Mill Yard, Brenhill, Wales, CF00 1AB.</p>
  <p>© 2025 Valtorix Mechanical Design | All Rights Reserved</p>
</div>
</body>
</html>
```